Timber Crest Construction Needs business card

Hey we are in need of business card designs. I have upload our logo as a guideline, but free feel to run with it or come up with something unique.
Pls have fun with it and be creative. the name says it all!
i will give some directions after i see a few entries..
Updates
Logo source file has been uploaded..
Hey because of the logo is so colourful already.
Can we have a few submissions with less colour.
Also we are looking for clever/hidden/descriptive business card.

```html
<!DOCTYPE html>
<html lang="en">
<head>
<meta charset="utf-8">
<title>Timber Crest Construction – Business Card</title>
<link rel="stylesheet" href="https://fonts.googleapis.com/css2?family=Didact+Gothic&display=swap">
<style>
  :root {
    --backdrop: #1f8a06;
    --card: #ffffff;
    --ink: #1b1b1b;
    --grey: #7a7b7e;
    --accent-red: #e3212b;
    --accent-yellow: #f7c600;
    --accent-blue: #1a7fce;
    --band: #191919;
  }
  * { margin: 0; padding: 0; box-sizing: border-box; }
  html, body { width: 1200px; height: 1200px; overflow: hidden; }
  body {
    background: var(--backdrop);
    font-family: "Didact Gothic", "Century Gothic", sans-serif;
    position: relative;
  }
  .card {
    position: absolute;
    left: 212px;
    width: 800px;
    height: 445px;
    background: var(--card);
    overflow: hidden;
  }
  .card--front { top: 130px; }
  .card--back  { top: 641px; }

  .wordmark {
    position: absolute;
    display: flex;
    flex-direction: column;
    align-items: center;
  }
  .wordmark__square {
    width: 34px;
    height: 34px;
    background: var(--accent-blue);
    margin-bottom: 16px;
  }
  .wordmark__name {
    color: var(--grey);
    font-size: 34px;
    letter-spacing: 2px;
    line-height: 1.1;
    text-align: center;
    text-transform: uppercase;
  }
  .card--front .wordmark { left: 0; right: 0; top: 150px; }
  .card--back .wordmark { left: 40px; width: 320px; top: 130px; }

  .details {
    position: absolute;
    left: 436px;
    top: 76px;
    color: var(--ink);
    letter-spacing: 3px;
    text-transform: uppercase;
  }
  .details__name { font-size: 15px; letter-spacing: 4px; -webkit-text-stroke: 0.4px var(--ink); }
  .details__role { font-size: 14px; color: var(--accent-red); margin-top: 4px; }
  .details__address { font-size: 14px; margin-top: 38px; line-height: 21px; letter-spacing: 2.8px; }

  .contacts {
    position: absolute;
    left: 436px;
    top: 234px;
    list-style: none;
  }
  .contacts__item {
    display: flex;
    align-items: center;
    height: 25.3px;
    font-size: 14.5px;
    letter-spacing: 1.9px;
    color: var(--ink);
  }
  .contacts__icon { width: 16px; height: 16px; margin-right: 20px; margin-left: -1px; }

  .wave { position: absolute; left: 0; bottom: 0; width: 800px; height: 445px; }
</style>
</head>
<body>
  <section class="card card--front">
    <div class="wordmark">
      <div class="wordmark__square"></div>
      <div class="wordmark__name">Timber Crest<br>Construction</div>
    </div>
  </section>

  <section class="card card--back">
    <div class="wordmark">
      <div class="wordmark__square"></div>
      <div class="wordmark__name">Timber Crest<br>Construction</div>
    </div>

    <div class="details">
      <p class="details__name">Marta Quinlan</p>
      <p class="details__role">Director</p>
      <p class="details__address">Unit 3, 212-216 Harlow Street<br>Greenvale North</p>
    </div>

    <ul class="contacts">
      <li class="contacts__item">
        <svg class="contacts__icon" viewBox="0 0 16 16" aria-hidden="true"><path d="M1 6 C1 2 15 2 15 6 L12 7 L11 5 L5 5 L4 7 Z M4 8 L12 8 L14 14 L2 14 Z" fill="var(--accent-red)"/><circle cx="8" cy="11" r="1.8" fill="#fff"/></svg>
        <span>9718 2254</span>
      </li>
      <li class="contacts__item">
        <svg class="contacts__icon" viewBox="0 0 16 16" aria-hidden="true"><rect x="4" y="1" width="8" height="5" fill="none" stroke="var(--accent-red)" stroke-width="1.5"/><rect x="1" y="6" width="14" height="6" rx="1" fill="var(--accent-red)"/><rect x="4" y="10" width="8" height="5" fill="#fff" stroke="var(--accent-red)" stroke-width="1.5"/></svg>
        <span>9718 2260</span>
      </li>
      <li class="contacts__item">
        <svg class="contacts__icon" viewBox="0 0 16 16" aria-hidden="true"><rect x="1" y="3.5" width="14" height="9" fill="none" stroke="var(--accent-red)" stroke-width="1.5"/><path d="M1 3.5 L8 9 L15 3.5" fill="none" stroke="var(--accent-red)" stroke-width="1.5"/></svg>
        <span>marta@timbercrestbuild.com</span>
      </li>
      <li class="contacts__item">
        <svg class="contacts__icon" viewBox="0 0 16 16" aria-hidden="true"><circle cx="8" cy="8" r="6.5" fill="none" stroke="var(--accent-red)" stroke-width="1.5"/><path d="M1.5 8 H14.5 M8 1.5 C4 5 4 11 8 14.5 M8 1.5 C12 5 12 11 8 14.5" fill="none" stroke="var(--accent-red)" stroke-width="1.2"/></svg>
        <span>www.timbercrestbuild.com</span>
      </li>
    </ul>

    <svg class="wave" viewBox="0 0 800 445" aria-hidden="true">
      <path class="wave__yellow" d="M0 355 C200 336 400 392 560 421 L800 445 L0 445 Z" fill="var(--accent-yellow)"/>
      <path class="wave__red" d="M460 418 C620 430 720 386 800 338 L800 445 L460 445 Z" fill="var(--accent-red)"/>
      <path class="wave__band" d="M0 372 C200 350 380 395 548 418 C650 431 730 395 800 354 L800 445 L0 445 Z" fill="var(--band)"/>
    </svg>
  </section>
</body>
</html>
```